BuildLinkHub.com Full Stationery Design

Business Card will have all info on it. Letterhead will not have name, title or mobile number. Keep general feeling very clean, using colors from the logo as accents.
Name:Dale Marchetti
Title:President
Phone: 1-800-555-0142
Cell: 306-555-0187
email: dale@buildlinkhub.example
website: www.buildlinkhub.example
Address:
PO Box 947
Warman, SK
S0J2T0

Target Market(s)

Construction Business owners

Industry/Entity Type

Business

Contact Information for Business Card

Name:Dale Marchetti
Title:President
Phone: 1-800-555-0142
Cell: 306-555-0187
Address:
PO Box 947
Warman, SK
S0J2T0

Font styles to use
Sans Serif

Requirements
Must have
• Clean look
Should not have
• Images or cartoon type characters or tools

```html
<!DOCTYPE html>
<html lang="en">
<head>
<meta charset="utf-8">
<title>BuildLinkHub.com – Business Card</title>
<link rel="stylesheet" href="https://fonts.googleapis.com/css2?family=Open+Sans:wght@400;600&display=swap">
<style>
  :root {
    --backdrop: #5a4a3c;
    --slate: #4a596a;
    --orange: #ee4b2b;
    --white: #ffffff;
    --soft-white: #f3f5f7;
  }
  html, body {
    margin: 0;
    padding: 0;
    width: 1200px;
    height: 987px;
    overflow: hidden;
    background: var(--backdrop);
    font-family: "Open Sans", Arial, sans-serif;
  }
  .canvas {
    position: relative;
    width: 1200px;
    height: 987px;
  }
  .card {
    position: absolute;
    left: 293px;
    width: 615px;
    height: 352px;
    box-shadow: 0 2px 6px rgba(0,0,0,0.35);
    overflow: hidden;
  }
  .card-front { top: 130px; background: var(--white); }
  .card-back  { top: 506px; background: var(--slate); }

  .wordmark {
    position: absolute;
    left: 0;
    right: 0;
    display: flex;
    align-items: center;
    justify-content: center;
    gap: 14px;
    font-weight: 600;
    letter-spacing: 0.2px;
  }
  .wordmark-mark {
    width: 34px;
    height: 34px;
    background: var(--orange);
  }
  .card-front .wordmark { top: 74px; font-size: 40px; color: var(--slate); }
  .card-back .wordmark  { top: 128px; font-size: 40px; color: var(--white); }
  .card-back .wordmark-mark { background: var(--white); }

  .band {
    position: absolute;
    top: 197px;
    height: 134px;
    color: var(--white);
    box-sizing: border-box;
  }
  .band-identity {
    left: 0;
    width: 307px;
    background: var(--slate);
    padding: 16px 0 0 29px;
  }
  .band-contact {
    left: 309px;
    width: 306px;
    background: var(--orange);
    padding: 17px 18px 0 0;
  }
  .person-name { font-size: 22px; font-weight: 600; line-height: 28px; margin: 0; }
  .person-title { font-size: 16px; line-height: 22px; margin: 0 0 4px; }
  .address { font-size: 15.5px; line-height: 22px; margin: 0 0 0 2px; font-style: normal; }

  .contact-list { list-style: none; margin: 0; padding: 0; }
  .contact-list li {
    display: flex;
    justify-content: flex-end;
    align-items: center;
    gap: 8px;
    font-size: 15.5px;
    line-height: 23.5px;
  }
  .contact-list svg { width: 15px; height: 15px; fill: var(--white); flex: none; }

  .back-url {
    position: absolute;
    top: 194px;
    left: 0;
    right: 0;
    text-align: center;
    color: var(--soft-white);
    font-size: 17px;
  }
</style>
</head>
<body>
<main class="canvas">
  <section class="card card-front" aria-label="Business card front">
    <div class="wordmark"><span class="wordmark-mark"></span><span>BuildLinkHub.com</span></div>
    <div class="band band-identity">
      <p class="person-name">Dale Marchetti</p>
      <p class="person-title">President</p>
      <address class="address">PO Box 947<br>Warman, SK, S0J2T0</address>
    </div>
    <div class="band band-contact">
      <ul class="contact-list">
        <li>1-800-555-0142
          <svg viewBox="0 0 24 24" aria-hidden="true"><path d="M6.6 10.8a15.1 15.1 0 0 0 6.6 6.6l2.2-2.2c.3-.3.7-.4 1-.2 1.1.4 2.3.6 3.6.6.6 0 1 .4 1 1V20c0 .6-.4 1-1 1A17 17 0 0 1 3 4c0-.6.4-1 1-1h3.5c.6 0 1 .4 1 1 0 1.3.2 2.5.6 3.6.1.3 0 .7-.2 1z"/></svg></li>
        <li>306-555-0187
          <svg viewBox="0 0 24 24" aria-hidden="true"><path d="M7 1h10a2 2 0 0 1 2 2v18a2 2 0 0 1-2 2H7a2 2 0 0 1-2-2V3a2 2 0 0 1 2-2zm0 3v15h10V4zm5 16.2a.9.9 0 1 0 0 1.8.9.9 0 0 0 0-1.8z"/></svg></li>
        <li>dale@buildlinkhub.example
          <svg viewBox="0 0 24 24" aria-hidden="true"><path d="M2 5h20v14H2zm2 2v.5l8 5 8-5V7zm0 2.8V17h16V9.8l-8 5z"/></svg></li>
        <li>www.buildlinkhub.example
          <svg viewBox="0 0 24 24" aria-hidden="true"><path d="M12 2a10 10 0 1 0 0 20 10 10 0 0 0 0-20zm-1 17.9A8 8 0 0 1 4.2 10L9 15v1a2 2 0 0 0 2 2zm6.9-2.5A2 2 0 0 0 16 16h-1v-3a1 1 0 0 0-1-1H8v-2h2a1 1 0 0 0 1-1V7h2a2 2 0 0 0 2-2v-.4a8 8 0 0 1 2.9 12.8z"/></svg></li>
      </ul>
    </div>
  </section>

  <section class="card card-back" aria-label="Business card back">
    <div class="wordmark"><span class="wordmark-mark"></span><span>BuildLinkHub.com</span></div>
    <p class="back-url">www.buildlinkhub.example</p>
  </section>
</main>
</body>
</html>
```